SkyvornQ Business Cards and Stationary Design

Need a design for our business cards and stationary. I want to carry on the theme of the logo. I want the business cards to have a design on the back. I would like the business cards and the stationary to carry the same theme, design scheme, and branding

Target Market(s)

Airlines and Maintenance Facilities

Industry/Entity Type

Aviation

Contact Information for Business Card

Name
Position Title
Address: 4827 Trellis Hollow Road, Marlow Bay, Ostara, 34951
Office Number
Mobile Number
Email
Website

Font styles to use
Serif
Sans Serif

Colors

Designer to choose colors to be used in the design.

```html
<!DOCTYPE html>
<html lang="en">
<head>
<meta charset="utf-8">
<title>SkyvornQ Business Card</title>
<link rel="stylesheet" href="https://fonts.googleapis.com/css2?family=Montserrat:wght@600;700;800&family=Nunito+Sans:wght@400;600&display=swap">
<style>
  :root {
    --bg: #3a3330;
    --navy: #1f3560;
    --navy-soft: #2c4577;
    --ink: #1c2a4a;
    --text: #3a3d44;
    --accent: #2f8fd8;
    --card-white: #f7f7f7;
    --rule: #b9bcc2;
  }
  * { margin: 0; padding: 0; box-sizing: border-box; }
  html, body { width: 1200px; height: 862px; overflow: hidden; }
  body {
    background: var(--bg);
    position: relative;
    font-family: "Nunito Sans", Arial, sans-serif;
  }
  .card {
    position: absolute;
    width: 560px;
    height: 320px;
    border-radius: 4px;
    box-shadow: 0 10px 24px rgba(0,0,0,.35);
  }
  .card-back {
    left: 60px; top: 100px;
    background: var(--navy);
    display: flex; align-items: center; justify-content: center; gap: 22px;
  }
  .back-mark {
    width: 110px; height: 110px; border-radius: 50%;
    border: 10px solid var(--navy-soft);
  }
  .back-name {
    font-family: "Montserrat", Arial, sans-serif;
    font-weight: 800;
    font-size: 34px;
    letter-spacing: 6px;
    color: var(--navy-soft);
  }
  .card-front {
    left: 580px; top: 440px;
    background: var(--card-white);
    display: flex; align-items: center;
  }
  .brand {
    width: 270px;
    display: flex; flex-direction: column; align-items: center; gap: 14px;
  }
  .brand-mark {
    width: 58px; height: 58px; border-radius: 50%;
    border: 6px solid var(--accent);
  }
  .brand-name {
    font-family: "Montserrat", Arial, sans-serif;
    font-weight: 800;
    font-size: 25px;
    letter-spacing: 5px;
    color: var(--ink);
  }
  .divider {
    width: 1px; height: 170px; background: var(--rule);
  }
  .contact {
    padding-left: 26px;
    color: var(--text);
    font-size: 14px;
    line-height: 1.35;
  }
  .person-name {
    font-family: "Montserrat", Arial, sans-serif;
    font-weight: 700; font-size: 22px; color: #2e3036;
  }
  .person-role { font-size: 15px; margin-bottom: 10px; }
  .address { margin-bottom: 8px; }
  .contact-list { list-style: none; }
  .contact-list li { display: flex; align-items: center; gap: 9px; }
  .contact-list svg { width: 13px; height: 13px; flex: none; }
</style>
</head>
<body>
  <section class="card card-back" aria-label="Card back">
    <div class="back-mark"></div>
    <div class="back-name">SKYVORNQ</div>
  </section>

  <section class="card card-front" aria-label="Card front">
    <div class="brand">
      <div class="brand-mark"></div>
      <div class="brand-name">SKYVORNQ</div>
    </div>
    <div class="divider"></div>
    <div class="contact">
      <div class="person-name">Darren KOLBY</div>
      <div class="person-role">CEO / Founder</div>
      <div class="address">4827 Trellis Hollow Road<br>Marlow Bay, Ostara, 34951</div>
      <ul class="contact-list">
        <li><svg viewBox="0 0 16 16"><path d="M4 1l3 3-2 2c1 2 3 4 5 5l2-2 3 3-2 3C7 15 1 9 1 4z" fill="none" stroke="var(--accent)" stroke-width="1.5"/></svg>000.000.0000</li>
        <li><svg viewBox="0 0 16 16"><rect x="4" y="1" width="8" height="14" rx="1.5" fill="none" stroke="var(--accent)" stroke-width="1.5"/></svg>000.000.0000</li>
        <li><svg viewBox="0 0 16 16"><rect x="1" y="3" width="14" height="10" fill="none" stroke="var(--accent)" stroke-width="1.5"/><path d="M1 3l7 6 7-6" fill="none" stroke="var(--accent)" stroke-width="1.5"/></svg>darren@skyvornq.com</li>
        <li><svg viewBox="0 0 16 16"><circle cx="8" cy="8" r="6.5" fill="none" stroke="var(--accent)" stroke-width="1.5"/><path d="M1.5 8h13M8 1.5c-3 3-3 10 0 13M8 1.5c3 3 3 10 0 13" fill="none" stroke="var(--accent)" stroke-width="1.2"/></svg>www.skyvornq.com</li>
      </ul>
    </div>
  </section>
</body>
</html>
```